Kestrada LLC, needs a web page no more than 5 pages (for now)

Kestrada is a general contractor. Our services include general contracting, design-build construction, disaster recovery and environmental remediation. Our main clients are PMX, TQ, State and Local Gov't Agencies, Hospitals and Schools. Kestrada is also a SDVOSB.

```html
<!DOCTYPE html>
<html lang="en">
<head>
<meta charset="utf-8">
<title>Kestrada LLC — General Contractor</title>
<link href="https://fonts.googleapis.com/css2?family=Montserrat:wght@500;600;700;800&family=Mulish:wght@400;600;700&display=swap" rel="stylesheet">
<style>
:root{
  --brown:#8a4f1f;
  --brown-dark:#6b3a14;
  --gold:#c98a36;
  --gold-light:#e2a650;
  --cream:#fbf3e6;
  --ink:#111111;
  --text:#333333;
  --muted:#666666;
  --white:#ffffff;
  --black:#0b0b0b;
}
*{box-sizing:border-box;margin:0;padding:0}
html,body{width:1200px;height:4491px;overflow:hidden}
body{position:relative;background:var(--white);font-family:'Mulish',sans-serif;color:var(--text)}
section,header,footer{position:absolute;left:0;width:1200px}
.abs{position:absolute}
.heading{font-family:'Montserrat',sans-serif;font-weight:800;color:var(--ink);text-transform:uppercase;line-height:1.15}
.accent{color:var(--gold)}
.rule{position:absolute;width:46px;height:2px;background:var(--brown)}
.btn{position:absolute;display:flex;align-items:center;justify-content:center;border-radius:30px;background:var(--gold-light);color:var(--ink);font-family:'Montserrat',sans-serif;font-weight:700;text-transform:uppercase}
.photo{position:absolute;border-radius:16px}

/* hero */
.hero{top:0;height:656px;background:linear-gradient(180deg,#8e9eae 0%,#c9a57b 35%,#8a5a30 70%,#4a2e18 100%)}
.hero-shade{position:absolute;inset:0;background:linear-gradient(90deg,rgba(30,18,8,.45) 0%,rgba(30,18,8,0) 60%)}
.brand{position:absolute;left:148px;top:60px;display:flex;align-items:center;gap:10px;font-family:'Montserrat',sans-serif;font-weight:700;font-size:30px;color:var(--white);letter-spacing:1px}
.brand i{display:block;width:14px;height:14px;border-radius:50%;background:var(--gold)}
.nav{position:absolute;top:36px;left:388px;display:flex;align-items:center;gap:28px;font-family:'Montserrat',sans-serif;font-weight:600;font-size:12.5px;color:var(--ink);text-transform:uppercase}
.nav .active{background:var(--brown);color:var(--white);padding:6px 12px;border-radius:20px}
.phone-pill{position:absolute;left:877px;top:34px;width:173px;height:36px;border:1.5px solid var(--ink);border-radius:20px;display:flex;align-items:center;justify-content:center;gap:8px;font-family:'Montserrat',sans-serif;font-weight:600;font-size:14px;color:var(--ink)}
.hero-title{position:absolute;left:148px;top:392px;font-family:'Montserrat',sans-serif;font-weight:800;font-size:35px;line-height:45px;color:var(--white);text-transform:uppercase}
.dots{position:absolute;left:558px;top:602px;display:flex;gap:13px}
.dots span{width:11px;height:11px;border-radius:50%;border:1.5px solid var(--white)}
.dots span:first-child{background:var(--gold-light);border-color:var(--gold-light)}

/* about */
.about{top:656px;height:565px}
.about p{position:absolute;left:606px;top:268px;width:450px;font-size:14.5px;line-height:24px;color:var(--text)}

/* stats */
.stats{top:1221px;height:134px;background:linear-gradient(90deg,var(--brown) 0%,#b57a34 50%,var(--gold-light) 100%);color:var(--white)}
.stat{position:absolute;top:30px;text-align:center}
.stat b{display:block;font-family:'Montserrat',sans-serif;font-weight:700;font-size:38px;line-height:44px}
.stat span{font-size:14px;font-weight:600}
.stat-div{position:absolute;top:36px;width:1px;height:66px;background:rgba(255,255,255,.7)}

/* services */
.services{top:1355px;height:532px}
.tag{position:absolute;left:150px;top:90px;padding:7px 18px;border-radius:20px;background:var(--cream);font-family:'Montserrat',sans-serif;font-weight:700;font-size:13px;color:var(--ink)}
.services p{position:absolute;left:152px;top:270px;width:318px;font-size:12.5px;line-height:20px}
.tab-line{position:absolute;top:75px;width:2px;height:384px;background:#555}
.tab-label{position:absolute;font-family:'Montserrat',sans-serif;font-weight:700;font-size:15px;color:var(--ink);writing-mode:vertical-rl;transform:rotate(180deg);bottom:72px}

/* industries */
.industries{top:1887px;height:572px;background:var(--cream)}
.card-cap{position:absolute;top:490px;width:211px;text-align:center;font-size:14px;line-height:21px;color:var(--ink);font-weight:600}

/* sdvosb */
.veteran{top:2459px;height:230px;background:linear-gradient(90deg,#2a2a2e,#3b3630 50%,#2a2a2e)}
.veteran h2{position:absolute;left:0;width:1200px;top:88px;text-align:center;font-family:'Montserrat',sans-serif;font-weight:600;font-size:36px;color:var(--white)}

/* projects */
.projects{top:2689px;height:532px}
.arrow-box{position:absolute;top:93px;width:27px;height:27px;border:1.5px solid var(--ink);border-radius:6px;display:flex;align-items:center;justify-content:center}
.proj-title{position:absolute;top:432px;width:218px;text-align:center;font-size:14px;font-weight:700;color:var(--ink)}
.proj-sub{position:absolute;top:455px;width:218px;text-align:center;font-size:11px;color:var(--muted)}

/* testimonial */
.testimonial{top:3221px;height:471px;background:linear-gradient(135deg,#8a5524 0%,#a66a2e 50%,#7a4a1e 100%)}
.testimonial blockquote{position:absolute;left:218px;top:163px;width:800px;font-size:26.5px;line-height:32px;color:var(--white);font-weight:600}
.testimonial cite{position:absolute;left:218px;top:376px;font-style:normal;font-size:15px;font-weight:700;color:var(--white)}

/* values */
.values{top:3692px;height:441px}
.values p{position:absolute;left:158px;top:164px;width:884px;text-align:center;font-size:15px;line-height:24px}
.value-icon{position:absolute;top:268px}
.value{position:absolute;top:350px;width:240px;text-align:center;font-family:'Montserrat',sans-serif;font-weight:700;font-size:16px;color:var(--ink)}
.value-div{position:absolute;top:272px;width:2px;height:112px;background:var(--gold)}

/* footer */
.site-footer{top:4133px;height:358px;background:var(--black);color:var(--white)}
.foot-h{position:absolute;top:47px;font-family:'Montserrat',sans-serif;font-weight:700;font-size:14px;text-transform:uppercase}
.foot-list{position:absolute;list-style:none;font-size:12px;line-height:19.5px}
.contact-row{position:absolute;left:415px;display:flex;gap:14px;font-size:12.5px;line-height:19px}
.socials{position:absolute;left:849px;top:84px;display:flex;gap:5px}
.socials span{width:24px;height:24px;border-radius:50%;background:var(--gold-light)}
.enquire{position:absolute;left:849px;top:143px;width:197px;height:51px;border-radius:8px;background:var(--brown);display:flex;align-items:center;justify-content:center;font-family:'Montserrat',sans-serif;font-weight:700;font-size:17px;text-transform:uppercase}
.copyright{position:absolute;top:297px;left:0;width:1200px;text-align:center;font-size:12px;color:#cfcfcf}
</style>
</head>
<body>

<header class="hero">
  <div class="abs" style="inset:0" role="img" aria-label="Construction site at sunset with excavators and three engineers in hard hats reviewing plans"></div>
  <div class="hero-shade"></div>
  <div class="brand"><i></i>KESTRADA</div>
  <nav class="nav">
    <span class="active">Home</span><span>About Us</span><span>Services</span><span>Our Work</span><span>Contact Us</span>
  </nav>
  <div class="phone-pill">
    <svg width="16" height="16" viewBox="0 0 24 24" fill="none" stroke="#111" stroke-width="2"><path d="M5 3h4l2 5-2.5 1.5a11 11 0 0 0 6 6L16 13l5 2v4a2 2 0 0 1-2 2A16 16 0 0 1 3 5a2 2 0 0 1 2-2z"/></svg>
    (555) 014 2290
  </div>
  <h1 class="hero-title"><span class="accent">Building</span> with<br>integrity. Serving<br>with <span class="accent">purpose.</span></h1>
  <div class="btn" style="left:148px;top:548px;width:162px;height:42px;font-size:14px">Contact Us</div>
  <div class="dots"><span></span><span></span><span></span><span></span></div>
</header>

<section class="about">
  <div class="photo" style="left:150px;top:71px;width:201px;height:431px;background:linear-gradient(180deg,#9fb2c4,#8a7a55 60%,#6c5a3c)" role="img" aria-label="Two construction managers in hard hats reviewing plans beside scaffolding"></div>
  <div class="photo" style="left:366px;top:71px;width:199px;height:210px;background:linear-gradient(180deg,#c9cbd0,#b39a74)" role="img" aria-label="Worker in safety vest guiding a timber frame into place"></div>
  <div class="photo" style="left:366px;top:294px;width:199px;height:208px;background:linear-gradient(180deg,#7d8ea0,#6d5d4c 60%,#4a3d30)" role="img" aria-label="Worker in orange jacket overlooking an industrial site"></div>
  <h2 class="heading abs" style="left:606px;top:63px;font-size:35px;line-height:46px">We <span class="accent">love to build.</span><br>It’s who we are and<br>what we do.</h2>
  <div class="rule" style="left:607px;top:220px"></div>
  <p>Lorem ipsum dolor sit amet, consectetur adipiscing elit, sed do eiusmod tempor incididunt ut labore et dolore magna aliqua. Ut enim ad minim veniam, quis nostrud exercitation ullamco laboris nisi ut aliquip ex ea commodo consequat. Duis aute irure dolor in reprehenderit in voluptate velit esse cillum dolore eu fugiat nulla pariatur. Excepteur sint occaecat cupidatat non proident, sunt in culpa qui officia deserunt mollit anim id est laborum.</p>
  <div class="btn" style="left:607px;top:462px;width:150px;height:38px;font-size:13px">Read More</div>
</section>

<section class="stats">
  <div class="stat" style="left:148px;width:110px;text-align:left"><b>75%</b><span>Repeat Clients</span></div>
  <div class="stat-div" style="left:312px"></div>
  <div class="stat" style="left:360px;width:150px"><b>7500</b><span>Projects &amp; counting</span></div>
  <div class="stat-div" style="left:575px"></div>
  <div class="stat" style="left:620px;width:150px"><b>20</b><span>Years of Experience</span></div>
  <div class="stat-div" style="left:825px"></div>
  <div class="stat" style="left:880px;width:180px"><b>2,300</b><span>Associates Nationwide</span></div>
</section>

<section class="services">
  <div class="tag">OUR SERVICES</div>
  <svg class="abs" style="left:348px;top:72px" width="76" height="64" viewBox="0 0 76 64" fill="none" stroke="#8a4f1f" stroke-width="2.2" stroke-linecap="round" stroke-linejoin="round">
    <rect x="20" y="4" width="34" height="26" rx="3"/>
    <path d="M31 17l5 5 9-9"/>
    <path d="M6 40l12-8 10 4 10-2 14 10-10 8-14-8M70 40l-12-8-10 2"/>
    <path d="M26 46l-6 6M32 50l-6 6M38 54l-4 4"/>
  </svg>
  <h2 class="heading abs" style="left:150px;top:150px;font-size:33px;line-height:40px">General<br>Contracting</h2>
  <div class="rule" style="left:152px;top:242px"></div>
  <p>Sed ut perspiciatis unde omnis iste natus error sit voluptatem accusantium doloremque laudantium, totam rem aperiam, eaque ipsa quae ab illo inven tore veritatis et quasi architecto beatae vitae dicta sunt explicabo. Nemo enim ipsam voluptatem quia voluptas sit aspernatur aut odit aut fugit, sed quia consequuntur magni dolores eos qui ratione.</p>
  <div class="btn" style="left:152px;top:436px;width:112px;height:30px;font-size:11px">Read More</div>
  <div class="photo" style="left:516px;top:70px;width:260px;height:397px;background:linear-gradient(180deg,#c4a47c,#8d6a45 50%,#4e4a55)" role="img" aria-label="Carpenter in hard hat and plaid shirt measuring a timber wall frame"></div>
  <div class="tab-line" style="left:818px"></div>
  <div class="tab-line" style="left:898px"></div>
  <div class="tab-line" style="left:973px"></div>
  <div class="tab-line" style="left:1050px"></div>
  <div class="tab-label" style="left:845px">DESIGN-BUILD CONSTRUCTION</div>
  <div class="tab-label" style="left:924px;color:var(--gold)">DISASTER RECOVERY</div>
  <div class="tab-label" style="left:1002px">ENVIRONMENTAL REMEDIATION</div>
</section>

<section class="industries">
  <h2 class="heading abs" style="left:0;width:1200px;top:62px;text-align:center;font-size:33px;line-height:42px"><span style="color:var(--brown)">Design-build experts</span> in<br>various industries</h2>
  <div class="rule" style="left:577px;top:152px"></div>
  <div class="photo" style="left:152px;top:199px;width:211px;height:263px;background:linear-gradient(180deg,#6e9ccf,#d8cdb8 60%,#6c8a4a)" role="img" aria-label="State capitol building with dome under blue sky"></div>
  <div class="photo" style="left:384px;top:199px;width:211px;height:263px;background:linear-gradient(180deg,#8fb6df,#d9d6cf 55%,#a7a39a)" role="img" aria-label="Columned government building with a flag"></div>
  <div class="photo" style="left:614px;top:199px;width:209px;height:263px;background:radial-gradient(circle at 50% 45%,#7ee0e6,#1d5a6a 55%,#0d2a38)" role="img" aria-label="Cupped hands holding a glowing medical cross"></div>
  <div class="photo" style="left:842px;top:199px;width:211px;height:263px;background:linear-gradient(180deg,#b9a58a,#6f6a7a 60%,#2c3550)" role="img" aria-label="Students writing at desks in a classroom"></div>
  <div class="card-cap" style="left:152px">Federal<br>(PMX, TQ, NRA, etc.)</div>
  <div class="card-cap" style="left:384px">State &amp; Local<br>Government</div>
  <div class="card-cap" style="left:613px">Healthcare<br>(Hospitals &amp; Clinics)</div>
  <div class="card-cap" style="left:842px">Education<br>(K-12 &amp; Higher Ed)</div>
</section>

<section class="veteran" role="img" aria-label="Darkened photo of construction workers on a building site">
  <h2>Service-Disabled Veteran-Owned Small Business</h2>
</section>

<section class="projects">
  <h2 class="heading abs" style="left:150px;top:55px;font-size:32px"><span style="color:var(--brown)">Our</span> Projects</h2>
  <div class="rule" style="left:152px;top:108px"></div>
  <div class="arrow-box" style="left:976px;border-color:#aaa"><svg width="10" height="12" viewBox="0 0 10 12" fill="none" stroke="#aaa" stroke-width="2"><path d="M7 1L2 6l5 5"/></svg></div>
  <div class="arrow-box" style="left:1020px"><svg width="10" height="12" viewBox="0 0 10 12" fill="none" stroke="#111" stroke-width="2"><path d="M3 1l5 5-5 5"/></svg></div>
  <div class="photo" style="left:150px;top:150px;width:218px;height:262px;background:linear-gradient(180deg,#a9b8c7,#8a6a4e 55%,#6d5a46)" role="img" aria-label="Multi-storey building under construction with scaffolding"></div>
  <div class="photo" style="left:378px;top:150px;width:217px;height:262px;background:linear-gradient(180deg,#5a86b4,#e0a66a 55%,#6c4a2a)" role="img" aria-label="Excavators working on earth mounds at sunset"></div>
  <div class="photo" style="left:607px;top:150px;width:216px;height:262px;background:linear-gradient(180deg,#d8a94a,#c9b79c 55%,#e6e2da)" role="img" aria-label="Hard hat and blueprints on a desk with a laptop"></div>
  <div class="photo" style="left:835px;top:150px;width:217px;height:262px;background:linear-gradient(180deg,#d9dde2,#e4c24a 55%,#d96a2a)" role="img" aria-label="Engineers in hard hats reviewing building plans"></div>
  <div class="proj-title" style="left:150px">Lorem ipsum dolor sit</div><div class="proj-sub" style="left:150px">Sed ut perspiciatis</div>
  <div class="proj-title" style="left:378px">Lorem ipsum dolor sit</div><div class="proj-sub" style="left:378px">Sed ut perspiciatis</div>
  <div class="proj-title" style="left:607px">Lorem ipsum dolor sit</div><div class="proj-sub" style="left:607px">Sed ut perspiciatis</div>
  <div class="proj-title" style="left:835px">Lorem ipsum dolor sit</div><div class="proj-sub" style="left:835px">Sed ut perspiciatis</div>
</section>

<section class="testimonial" role="img" aria-label="Amber-tinted photo of workers on a construction site">
  <svg class="abs" style="left:216px;top:72px" width="64" height="50" viewBox="0 0 64 50" fill="#e2a650"><path d="M0 50V28C0 12 8 3 24 0l2 7C16 10 13 16 13 22h13v28zM36 50V28C36 12 44 3 60 0l2 7C52 10 49 16 49 22h13v28z"/></svg>
  <blockquote>Sed ut perspiciatis unde omnis iste natus error sit voluptatem accusantium doloremque laudantium, totam rem aperiam, eaque ipsa quae ab illo inven tore veritatis et quasi architecto beatae vitae dicta sunt explicabo. Nemo enim ipsam voluptatem quia voluptas sit aspernatur aut odit aut fugit, sed quia consequuntur magni dolores eos qui ratione.</blockquote>
  <cite>Daniel Orvell, United States</cite>
  <svg class="abs" style="left:962px;top:400px" width="34" height="14" viewBox="0 0 34 14" fill="none" stroke="#fff" stroke-width="2"><path d="M33 7H2M8 1L2 7l6 6"/></svg>
  <svg class="abs" style="left:1016px;top:400px" width="34" height="14" viewBox="0 0 34 14" fill="none" stroke="#fff" stroke-width="2"><path d="M1 7h31M26 1l6 6-6 6"/></svg>
</section>

<section class="values">
  <h2 class="heading abs" style="left:0;width:1200px;top:56px;text-align:center;font-size:33px">On <span class="accent">time.</span> On <span style="color:var(--brown)">budget.</span></h2>
  <p>Sed ut perspiciatis unde omnis iste natus error sit voluptatem accusantium doloremque laudantium, totam rem aperiam, eaque ipsa quae ab illo inven tore veritatis et quasi architecto beatae vitae dicta sunt explicabo. Nemo enim ipsam voluptatem quia voluptas sit aspernatur aut odit aut fugit, sed quia consequuntur magni dolores eos qui ratione.</p>
  <svg class="value-icon" style="left:311px" width="48" height="56" viewBox="0 0 48 56" fill="none" stroke="#8a4f1f" stroke-width="2"><circle cx="24" cy="20" r="16"/><path d="M24 11l3 6 6 1-4.5 4 1 6-5.5-3-5.5 3 1-6L15 18l6-1z"/><path d="M14 33l-6 18 8-3 4 7 4-15M34 33l6 18-8-3-4 7-4-15"/></svg>
  <div class="value-div" style="left:472px"></div>
  <svg class="value-icon" style="left:574px" width="48" height="56" viewBox="0 0 48 56" fill="none" stroke="#8a4f1f" stroke-width="2"><circle cx="26" cy="18" r="14"/><path d="M30 12h-6a3 3 0 0 0 0 6h4a3 3 0 0 1 0 6h-6M26 9v3M26 24v3"/><path d="M4 44l10-6h10l8 4H20M4 50l6 2h14l16-10-4-3-10 5"/></svg>
  <div class="value-div" style="left:716px"></div>
  <svg class="value-icon" style="left:820px" width="60" height="56" viewBox="0 0 60 56" fill="none" stroke="#8a4f1f" stroke-width="2"><circle cx="34" cy="28" r="20"/><circle cx="34" cy="28" r="15"/><path d="M34 18v10l7 5"/><path d="M2 22h10M4 28h8M2 34h10"/></svg>
  <div class="value" style="left:215px">Exceptional Quality</div>
  <div class="value" style="left:480px">Fixed Prices</div>
  <div class="value" style="left:730px">Efficient Timelines</div>
</section>

<footer class="site-footer">
  <div class="brand" style="top:126px;font-size:30px;left:150px;color:var(--white)"><i></i>KESTRADA</div>
  <div class="foot-h" style="left:415px">Contact Us</div>
  <div class="contact-row" style="top:92px">
    <svg width="12" height="16" viewBox="0 0 12 16" fill="#e2a650"><path d="M6 0a6 6 0 0 0-6 6c0 4.5 6 10 6 10s6-5.5 6-10a6 6 0 0 0-6-6zm0 8.5A2.5 2.5 0 1 1 6 3.5a2.5 2.5 0 0 1 0 5z"/></svg>
    <span>118 Larkspur Ave, Ste 4, Dunmore,<br>WY 82990 USA</span>
  </div>
  <div class="contact-row" style="top:148px">
    <svg width="14" height="14" viewBox="0 0 24 24" fill="#e2a650"><path d="M5 2h4l2 6-3 2a12 12 0 0 0 6 6l2-3 6 2v4a3 3 0 0 1-3 3A19 19 0 0 1 2 5a3 3 0 0 1 3-3z"/></svg>
    <span>+1 555 014 2290</span>
  </div>
  <div class="contact-row" style="top:187px">
    <svg width="15" height="12" viewBox="0 0 15 12" fill="#e2a650"><path d="M0 0h15v12H0z"/><path d="M0 0l7.5 6L15 0" stroke="#0b0b0b" fill="none" stroke-width="1.3"/></svg>
    <span>hello@kestradabuild.com</span>
  </div>
  <div class="foot-h" style="left:701px">Menu</div>
  <ul class="foot-list" style="left:701px;top:72px">
    <li>Home</li><li>About us</li><li>Categories</li><li>Products</li><li>Blog</li><li>Shop</li><li>Contact us</li>
  </ul>
  <div class="foot-h" style="left:849px;top:44px">Follow Us</div>
  <div class="socials"><span></span><span></span><span></span><span></span><span></span></div>
  <div class="enquire">Enquire Now</div>
  <div class="abs" style="left:150px;top:258px;width:900px;height:1px;background:#2a2a2a"></div>
  <div class="copyright">Copyright © 2025 All Rights Reserved</div>
</footer>

</body>
</html>
```